7K packaging design

We are a wholesaler for Automotive Spare Parts in Jordan and Iraq market and we needs to import spare parts from China under our company private brand "7K"
The 7K brand’s product lines include Filtration, Braking Systems, Wheels, Wheel Bolts & Nuts, Shock Absorbers, Sensors, Cooling Systems, Axles and more.
The aim of the project is to unify the brand packaging across all the product lines , we will start by the brake pads then based on the approved design we will do the other products

Target Market(s)

Jordan , Iraq Market

Industry/Entity Type

Automotive spare parts

Requirements
Must have
• Name of the product :Ceramic brake pads specs : Superior stopping power Noise suppression Low Dust Technology Made in china
Nice to have
• Brake pad outline image on the box
Should not have
• Blue color

```html
<!DOCTYPE html>
<html lang="en">
<head>
<meta charset="utf-8">
<title>7K packaging design – Ceramic Brake Pads dielines</title>
<link rel="stylesheet" href="https://fonts.googleapis.com/css2?family=Exo+2:ital,wght@0,800;1,800&family=Roboto:wght@500;700&display=swap">
<style>
  :root{
    --paper:#ffffff;
    --flap:#333333;
    --cut:#2aa6c0;
    --red:#ff0000;
    --red-mid:#d80000;
    --red-deep:#4a0000;
    --photo-light:#c9c9c9;
    --photo-dark:#4a4a4a;
    --strip-light:#d6d6d6;
    --strip-dark:#8c8c8c;
    --silver-hi:#ffffff;
    --silver-lo:#7a7a7a;
    --ink:#ffffff;
  }
  html,body{margin:0;padding:0;width:1200px;height:660px;overflow:hidden;background:var(--paper);}
  .canvas{display:block;width:1200px;height:660px;}
  .panel-flap{fill:var(--flap);}
  .cut{stroke:var(--cut);stroke-width:1.5;}
  .stop-red{stop-color:var(--red);}
  .stop-mid{stop-color:var(--red-mid);}
  .stop-deep{stop-color:var(--red-deep);}
  .stop-photo-light{stop-color:var(--photo-light);}
  .stop-photo-dark{stop-color:var(--photo-dark);}
  .stop-strip-light{stop-color:var(--strip-light);}
  .stop-strip-dark{stop-color:var(--strip-dark);}
  .stop-silver-hi{stop-color:var(--silver-hi);}
  .stop-silver-lo{stop-color:var(--silver-lo);}
  .product-name{font-family:"Exo 2",sans-serif;font-style:italic;font-weight:800;fill:var(--ink);}
  .brand-name{font-family:"Exo 2",sans-serif;font-style:normal;font-weight:800;fill:var(--ink);}
  .origin-note{font-family:"Roboto",sans-serif;font-weight:700;font-size:13px;fill:var(--ink);letter-spacing:.5px;}
  .feature-label{font-family:"Roboto",sans-serif;font-weight:500;font-size:7.5px;fill:var(--ink);}
  .feature-icon{fill:none;stroke:var(--ink);stroke-width:2;}
  .feature-icon-solid{fill:var(--ink);}
  .pad-outline-area{fill:rgba(255,255,255,.07);}
  .photo-area{fill:url(#g-photo);}
</style>
</head>
<body>
<svg class="canvas" viewBox="0 0 2576 1410" xmlns="http://www.w3.org/2000/svg">
  <defs>
    <linearGradient id="g-red-up" x1="0" y1="0" x2="0" y2="1">
      <stop offset="0" class="stop-deep"/><stop offset=".65" class="stop-mid"/><stop offset="1" class="stop-red"/>
    </linearGradient>
    <linearGradient id="g-red-down" x1="0" y1="0" x2="0" y2="1">
      <stop offset="0" class="stop-red"/><stop offset=".5" class="stop-red"/><stop offset="1" class="stop-deep"/>
    </linearGradient>
    <linearGradient id="g-red-diag" x1="0" y1="0" x2="1" y2="1">
      <stop offset="0" class="stop-deep"/><stop offset=".55" class="stop-red"/><stop offset="1" class="stop-red"/>
    </linearGradient>
    <linearGradient id="g-red-front" x1="0" y1="0" x2="1" y2="1">
      <stop offset="0" class="stop-red"/><stop offset=".6" class="stop-red"/><stop offset="1" class="stop-mid"/>
    </linearGradient>
    <linearGradient id="g-photo" x1="0" y1="0" x2="1" y2="1">
      <stop offset="0" class="stop-photo-light"/><stop offset="1" class="stop-photo-dark"/>
    </linearGradient>
    <linearGradient id="g-strip" x1="0" y1="0" x2="1" y2="0">
      <stop offset="0" class="stop-strip-dark"/><stop offset="1" class="stop-strip-light"/>
    </linearGradient>
    <linearGradient id="g-silver" x1="0" y1="0" x2="1" y2="0">
      <stop offset="0" class="stop-silver-lo"/><stop offset=".5" class="stop-silver-hi"/><stop offset="1" class="stop-silver-lo"/>
    </linearGradient>

    <!-- feature row: stopping power, noise suppression, low dust -->
    <g id="feature-row">
      <circle class="feature-icon" cx="13" cy="15" r="11"/>
      <circle class="feature-icon" cx="13" cy="15" r="5"/>
      <text class="feature-label" x="35" y="9">SUPERIOR</text>
      <text class="feature-label" x="35" y="16.5">STOPPING</text>
      <text class="feature-label" x="35" y="24">POWER</text>
      <path class="feature-icon-solid" d="M84 11h5l7-6v20l-7-6h-5z"/>
      <path class="feature-icon" d="M99 9l6-4M100 15h7M99 21l6 4"/>
      <text class="feature-label" x="108" y="13">NOISE</text>
      <text class="feature-label" x="108" y="20.5">SUPPRESSION</text>
      <circle class="feature-icon" cx="177" cy="15" r="10" stroke-dasharray="3 2"/>
      <circle class="feature-icon-solid" cx="174" cy="13" r="2"/>
      <circle class="feature-icon-solid" cx="180" cy="18" r="1.6"/>
      <text class="feature-label" x="193" y="13">LOW DUST</text>
      <text class="feature-label" x="193" y="20.5">TECHNOLOGY</text>
    </g>

    <!-- shared box artwork (without photo areas) -->
    <g id="box-dieline">
      <!-- lid row -->
      <rect class="panel-flap cut" x="70" y="72" width="278" height="238"/>
      <rect class="cut" x="348" y="72" width="589" height="238" fill="url(#g-red-up)"/>
      <rect class="panel-flap cut" x="937" y="72" width="278" height="238"/>
      <!-- top panel row -->
      <rect class="panel-flap cut" x="70" y="350" width="278" height="239"/>
      <rect class="cut" x="348" y="310" width="589" height="279" fill="url(#g-red-diag)"/>
      <rect class="panel-flap cut" x="937" y="350" width="278" height="239"/>
      <rect class="cut" x="158" y="573" width="100" height="16" fill="none"/>
      <rect class="cut" x="1027" y="573" width="100" height="16" fill="none"/>
      <!-- back panel (inverted) -->
      <polygon points="348,634 722,634 622,828 348,828" fill="url(#g-red-up)"/>
      <polygon points="348,589 745,589 722,634 348,634" fill="url(#g-strip)"/>
      <polygon points="745,589 762,589 640,828 622,828" fill="url(#g-silver)"/>
      <rect class="cut" x="348" y="589" width="589" height="239" fill="none"/>
      <use href="#feature-row" transform="rotate(180 540 612) translate(420 597)"/>
      <rect class="pad-outline-area" x="370" y="645" width="255" height="165" rx="30" role="img" aria-label="White line outline of two ceramic brake pads"/>
      <g transform="rotate(180 858 655)">
        <text class="product-name" x="800" y="641" font-size="26">Ceramic</text>
        <text class="product-name" x="800" y="664" font-size="26">Brake</text>
        <text class="product-name" x="800" y="687" font-size="26">Pads</text>
      </g>
      <text class="brand-name" x="868" y="793" font-size="52" text-anchor="middle" transform="rotate(180 868 775)">7K</text>
      <!-- front row -->
      <rect class="cut" x="70" y="828" width="278" height="227" fill="url(#g-red-down)"/>
      <rect class="cut" x="155" y="1055" width="108" height="11" fill="var(--red-deep)"/>
      <rect class="cut" x="348" y="828" width="589" height="277" fill="url(#g-red-front)"/>
      <rect class="cut" x="937" y="828" width="278" height="227" fill="url(#g-red-down)"/>
      <rect class="cut" x="1022" y="1055" width="108" height="11" fill="var(--red-deep)"/>
      <text class="brand-name" x="380" y="918" font-size="64">7K</text>
      <text class="product-name" x="375" y="999" font-size="24">Ceramic Brake Pads</text>
      <use href="#feature-row" x="375" y="1040"/>
      <rect class="pad-outline-area" x="615" y="870" width="300" height="195" rx="36" role="img" aria-label="White line outline of two ceramic brake pads"/>
      <!-- bottom row -->
      <path class="cut" d="M348 1105 L180 1105 Q136 1105 136 1150 Q150 1280 250 1330 Q290 1343 348 1343 Z" fill="url(#g-red-down)"/>
      <path class="cut" d="M937 1105 L1105 1105 Q1150 1105 1150 1150 Q1135 1280 1035 1330 Q995 1343 937 1343 Z" fill="url(#g-red-down)"/>
      <polygon points="662,1105 937,1105 937,1300 572,1300" fill="url(#g-red-up)"/>
      <polygon points="572,1300 937,1300 937,1343 550,1343" fill="url(#g-strip)"/>
      <polygon points="648,1105 664,1105 550,1343 534,1343" fill="url(#g-silver)"/>
      <rect class="cut" x="348" y="1105" width="589" height="238" fill="none"/>
      <rect class="pad-outline-area" x="660" y="1120" width="255" height="170" rx="30" role="img" aria-label="White line outline of two ceramic brake pads"/>
      <text class="brand-name" x="372" y="1180" font-size="54">7K</text>
      <text class="product-name" x="368" y="1266" font-size="27">Ceramic</text>
      <text class="product-name" x="368" y="1289" font-size="27">Brake</text>
      <text class="product-name" x="368" y="1312" font-size="27">Pads</text>
      <use href="#feature-row" transform="translate(605 1303) scale(1.2)"/>
    </g>
  </defs>

  <!-- dieline A: truck version -->
  <g class="dieline dieline-truck">
    <rect class="photo-area" x="70" y="589" width="278" height="239" role="img" aria-label="Greyscale photo of a commercial truck cab"/>
    <polygon class="photo-area" points="760,589 937,589 937,828 638,828" role="img" aria-label="Greyscale photo of a commercial truck cab"/>
    <rect class="photo-area" x="937" y="589" width="278" height="239" role="img" aria-label="Greyscale photo of a commercial truck cab"/>
    <polygon class="photo-area" points="348,1105 650,1105 536,1343 348,1343" role="img" aria-label="Greyscale photo of a commercial truck cab"/>
    <use href="#box-dieline"/>
    <g class="side-panel-text">
      <text class="origin-note" x="1077" y="618" text-anchor="middle" transform="rotate(180 1077 613)">MADE IN CHINA</text>
      <text class="product-name" x="1077" y="651" font-size="22" text-anchor="middle" transform="rotate(180 1077 643)">Ceramic Brake Pads</text>
      <text class="brand-name" x="1077" y="780" font-size="70" text-anchor="middle" transform="rotate(180 1077 757)">7K</text>
    </g>
  </g>

  <!-- dieline B: sports car version -->
  <g class="dieline dieline-car" transform="translate(1289 0)">
    <rect class="photo-area" x="70" y="589" width="278" height="239" role="img" aria-label="Greyscale photo of a sports car front wheel"/>
    <polygon class="photo-area" points="760,589 937,589 937,828 638,828" role="img" aria-label="Greyscale photo of a sports car front wheel"/>
    <rect class="photo-area" x="937" y="589" width="278" height="239" role="img" aria-label="Greyscale photo of a sports car front wheel"/>
    <polygon class="photo-area" points="348,1105 650,1105 536,1343 348,1343" role="img" aria-label="Greyscale photo of a sports car"/>
    <use href="#box-dieline"/>
    <g class="side-panel-text">
      <text class="origin-note" x="1077" y="618" text-anchor="middle" transform="rotate(180 1077 613)">MADE IN CHINA</text>
      <text class="product-name" x="1077" y="651" font-size="22" text-anchor="middle" transform="rotate(180 1077 643)">Ceramic Brake Pads</text>
      <text class="brand-name" x="1077" y="780" font-size="70" text-anchor="middle" transform="rotate(180 1077 757)">7K</text>
    </g>
  </g>
</svg>
</body>
</html>
```